Design the 21st Harborlight Open Cinema Showcase Poster. Think modern, chic, cool, film, movies - driving people to the film festival - the film festivla is in San Francisco and the SF East Bay. Our logo is attached. Dates will be determined soon . please use - November 2 - 11, 2018 (for placement) Keep in mind abstract, chic, modern - eye catching. website is www.hlocs-fest.org

Target Market(s)

25 - 45 year old - upper middle class

Industry/Entity Type

Film Production

Colors

Designer to choose colors to be used in the design.

Requirements
Must have
• logo (attached) www.hlocs-fest.org - chic modern design
Nice to have
• best coolest poster ever!
Should not have
• CLIP ART!!!

```html
<!DOCTYPE html>
<html lang="en">
<head>
<meta charset="utf-8">
<title>21st Harborlight Open Cinema Showcase Poster</title>
<link href="https://fonts.googleapis.com/css2?family=Montserrat:wght@300;500&display=swap" rel="stylesheet">
<style>
  :root {
    --page-bg: #ffffff;
    --red-deep: #7d1620;
    --red-mid: #a51d29;
    --red-bright: #b9222e;
    --shadow-red: #4a0c12;
    --text-white: #ffffff;
    --accent-green: #8cc63f;
  }
  html, body {
    margin: 0;
    padding: 0;
    width: 1200px;
    height: 806px;
    overflow: hidden;
    background: var(--page-bg);
    font-family: "Montserrat", Arial, sans-serif;
  }
  .poster {
    position: absolute;
    left: 331px;
    top: 23px;
    width: 537px;
    height: 760px;
    overflow: hidden;
    color: var(--text-white);
  }
  .poster__photo {
    position: absolute;
    inset: 0;
    background:
      radial-gradient(ellipse 40% 55% at 78% 35%, var(--shadow-red) 0%, rgba(74, 12, 18, 0) 70%),
      linear-gradient(160deg, var(--red-deep) 0%, var(--red-mid) 45%, var(--red-bright) 100%);
  }
  .brand {
    position: absolute;
    left: 46px;
    top: 40px;
  }
  .brand__dot {
    display: block;
    width: 34px;
    height: 34px;
    border-radius: 50%;
    background: var(--accent-green);
    margin-left: 54px;
    margin-bottom: 6px;
  }
  .brand__name {
    display: block;
    font-weight: 500;
    font-size: 40px;
    line-height: 1;
    letter-spacing: 2px;
  }
  .brand__presents {
    display: block;
    font-weight: 500;
    font-size: 16px;
    margin-top: 4px;
  }
  .title__edition {
    position: absolute;
    left: 42px;
    top: 346px;
    font-weight: 300;
    font-size: 140px;
    line-height: 1;
    letter-spacing: -4px;
  }
  .title__rule {
    position: absolute;
    left: 112px;
    top: 368px;
    width: 4px;
    height: 172px;
    background: var(--text-white);
  }
  .title__line {
    position: absolute;
    margin: 0;
    line-height: 1;
    white-space: nowrap;
  }
  .title__line--small {
    left: 126px;
    font-weight: 500;
    font-size: 34px;
  }
  .title__line--big {
    left: 110px;
    font-weight: 500;
    font-size: 64px;
    letter-spacing: -1px;
  }
  .title__line--one { top: 480px; }
  .title__line--two { top: 512px; }
  .title__line--three { top: 548px; }
  .title__line--four { top: 604px; }
  .dates {
    position: absolute;
    left: 111px;
    top: 670px;
    font-weight: 500;
    font-size: 30px;
    line-height: 1;
    white-space: nowrap;
  }
  .website {
    position: absolute;
    left: 0;
    right: 0;
    top: 726px;
    text-align: center;
    font-weight: 500;
    font-size: 17px;
    line-height: 1;
  }
</style>
</head>
<body>
  <main class="poster">
    <div class="poster__photo" role="img" aria-label="Photograph of a suspension bridge tower rising out of fog, tinted deep red"></div>

    <div class="brand">
      <span class="brand__dot"></span>
      <span class="brand__name">HLOCS</span>
      <span class="brand__presents">PRESENTS</span>
    </div>

    <div class="title__edition">21st</div>
    <div class="title__rule"></div>
    <h1 class="title">
      <span class="title__line title__line--small title__line--one">HARBORLIGHT</span>
      <span class="title__line title__line--small title__line--two">OPEN</span>
      <span class="title__line title__line--big title__line--three">CINEMA</span>
      <span class="title__line title__line--big title__line--four">SHOWCASE</span>
    </h1>
    <p class="dates">NOVEMBER 2 – 11, 2018</p>
    <p class="website">WWW.HLOCS-FEST.ORG</p>
  </main>
</body>
</html>
```